I need a website designed for my hair extensions business

I have some before and afters you can use

https://example-photos.net/p/Qm4trLwKoBa/

https://www.example-photos.net/p/Hvno7PaWkeR/?sid=QtPwZjN0cVhkYmRxUb==
Hi I offer tiny weave hair extensions
My instagram page is Virelahairextensionsstudio

I’m needing a Lux website
I have been doing weave hair extensions for 16 years and I specialise in only the finest installation and hair quality

The website must attract a high profile cliental

I have thousands of photos on my instagram page you can use

The website must be coded to attract hair extensions clients from all over Victoria Australia
It must have what’s relevant for google to recognise the website to Potential clients

recognise

Some are the below
Apologies for the confusion. Here are some SEO keywords that can be used for a website focused on Weave Hair Extensions in Victoria, Australia:

1. Weave hair extensions Victoria
2. Best weave hair extensions Australia
3. Affordable weave hair extensions
4. Professional weave hair extensions
5. High-quality weave hair extensions
6. Victoria weave hair extension services
7. Top-rated weave hair extension salon
8. Natural-looking weave hair extensions
9. Customizable weave hair extensions
10. Victoria's premier weave hair extensions

Remember to incorporate these keywords strategically into your website's content, including titles, headings, meta descriptions, and throughout the body text. This will help improve your website's visibility in search engine results and attract relevant traffic from individuals looking for weave hair extensions in Victoria, Australia.

Please make the website look elegant not tacky no pink or script writing please

Target Market(s)

Woman between 21 to 60

Industry/Entity Type

https://www.example-photos.net/reel/KpwwoTYBv7M/?sid=QtPwZjN0cVhkYmRxUb==

Coding

Coded - Design and coding required

Number of Pages Required

3 page

Requirements
Must have
• Description of myself 16 years experience, I’ve installed 1000s of weave hair extensions, my intention to deal is guaranteed.
Nice to have
• I have added 2 images or how flat and tiny the weave hair extensions are, here is a link to a video that can be used https://www.example-photos.net/reel/KpwwoTYBv7M/?sid=QtPwZjN0cVhkYmRxUb== The website should look elegant, the extensions I install are spectacular. You can see the before and after on my instagram page virela hair extensions studio. The pictures of my work should be taken from my instagram page as I own those photos
Should not have
• My website should not have pink or script writing it needs to attract a high cliental the website must look elegant

```html
<!DOCTYPE html>
<html lang="en">
<head>
<meta charset="utf-8">
<title>Virela Hair Extensions – Course Page Options</title>
<link href="https://fonts.googleapis.com/css2?family=Montserrat:wght@200;300;400;600&display=swap" rel="stylesheet">
<style>
:root{
  --board:#6b6b6b;
  --ink:#2b2b2b;
  --muted:#555;
  --copper:#c4906e;
  --copper-soft:#dcb89f;
  --blush:#f9efe9;
  --footer:#2c1c17;
  --footer-text:#d8cdc8;
  --subscribe:#e9b89a;
  --field:#3d2b25;
}
*{box-sizing:border-box;margin:0;padding:0}
html,body{width:1200px;height:1062px;overflow:hidden;background:var(--board)}
body{font-family:'Montserrat',sans-serif;color:var(--ink)}
.board{position:absolute;left:0;top:0;width:2044px;height:1809px;transform:scale(.58708);transform-origin:0 0;background:var(--board)}
.sample-label{position:absolute;top:104px;width:300px;text-align:center;color:#fff;font-weight:300;font-size:25px;letter-spacing:.5px}
.page{position:absolute;top:201px;width:495px;overflow:hidden;background:
  radial-gradient(circle at 100% 4%,#f3dccd 0,rgba(243,220,205,0) 70px),
  radial-gradient(circle at 0 10%,#f6e4d8 0,rgba(246,228,216,0) 80px),
  radial-gradient(circle at 5% 33%,#f8e7dc 0,rgba(248,231,220,0) 60px),
  radial-gradient(circle at 98% 55%,#f8e7dc 0,rgba(248,231,220,0) 55px),
  radial-gradient(circle at 97% 82%,#f6e1d4 0,rgba(246,225,212,0) 60px),
  radial-gradient(circle at 8% 90%,#f6e3d7 0,rgba(246,227,215,0) 70px),
  #fff}
.nav-link{position:absolute;top:28px;font-size:6.5px;color:#444;letter-spacing:.2px}
.nav-link.low{top:25px}
.nav-link.active{border-bottom:1px solid #333;padding-bottom:3px}
.brand{position:absolute;left:0;width:100%;text-align:center;font-weight:400;font-size:18px;letter-spacing:2px;line-height:1;color:var(--ink)}
.footer .brand{color:var(--footer-text)}
.arc{position:absolute;left:-40px;top:60px;width:76px;height:76px;border:1px solid #b98a6e;border-radius:50%}
.headline{position:absolute;left:0;width:100%;text-align:center;top:93px;font-size:14px;font-weight:400;letter-spacing:.2px}
.subhead{position:absolute;left:0;width:100%;text-align:center;top:114px;font-size:9.5px;font-weight:300}
.rule{position:absolute;top:133px;left:155px;width:185px;border-top:1px solid #555}
.intro{position:absolute;top:141px;left:110px;width:275px;text-align:center;font-size:6px;line-height:9.2px;color:#333}
.section-title{position:absolute;left:0;width:100%;text-align:center;top:187px;font-size:11.5px;font-weight:300}
.icon-box{position:absolute;width:78px;height:66px;border:1px solid var(--copper-soft);padding:3px}
.icon-box .art,.icon-circle .art{width:100%;height:100%;background:radial-gradient(circle,#f1dccd 0,#fbf4ef 70%,#fff 100%)}
.icon-circle{position:absolute;width:69px;height:69px;border:1px solid #3a2a24;border-radius:50%;padding:6px}
.icon-circle .art{border-radius:50%}
.num{position:absolute;font-weight:200;font-size:30px;color:#555;line-height:1}
.item{position:absolute;width:258px}
.item h3{font-size:9.5px;font-weight:300;margin-bottom:4px;letter-spacing:.1px}
.item p{font-size:6.1px;line-height:9.1px;color:#333}
.closing{position:absolute;left:95px;width:305px;text-align:center;font-size:8.8px;line-height:12.2px;font-weight:300}
.details{position:absolute;text-align:center}
.details h2{font-size:11.5px;font-weight:300;margin-bottom:12px}
.details p{font-size:7.6px;line-height:17.5px;color:#333}
.details b{font-weight:600}
.details-s1{left:82px;top:775px;width:331px;height:115px;background:var(--blush);border:1px solid var(--copper);outline:1px solid var(--copper);outline-offset:-4px;padding-top:20px;box-shadow:0 10px 12px -8px rgba(0,0,0,.12)}
.details-s2{left:0;top:721px;width:495px;height:145px;background:var(--blush);padding-top:40px}
.details-s3{left:119px;top:727px;width:257px;height:110px;border:1px dotted #333;padding-top:18px}
.form-title{position:absolute;left:0;width:100%;text-align:center;font-size:16px;font-weight:300;letter-spacing:.3px}
.form-sub{position:absolute;left:0;width:100%;text-align:center;font-size:9px;font-weight:300}
.form-box{position:absolute;left:82px;width:331px;border:1px solid var(--copper-soft)}
.line-field{position:absolute;width:123px;height:14px;border-bottom:1px solid #444;font-size:6px;color:#333}
.box-field{position:absolute;width:127px;height:20px;border:1px solid #777;background:#fff;font-size:5.8px;color:#333;padding:6px 0 0 5px}
.glyph{position:absolute;right:3px;font-size:6px;color:#777}
.submit{position:absolute;width:60px;height:21px;border:1px solid #333;background:#fff;font-size:7px;text-align:center;line-height:19px;letter-spacing:.3px}
.band{position:absolute;left:0;width:495px;background:linear-gradient(90deg,var(--blush),#fbf3ee 60%,#f6e2d6)}
.footer{position:absolute;left:0;width:495px;background:var(--footer);color:var(--footer-text)}
.f-col{position:absolute;font-size:5.8px;line-height:11px}
.f-col h4{font-size:8.4px;font-weight:300;letter-spacing:.3px;margin-bottom:7px;color:#eee}
.pin{display:inline-block;width:5px;margin-right:4px;color:var(--subscribe)}
.f-email{height:14px;background:var(--field);padding:3px 5px;font-size:5.5px;color:#ddd;width:112px}
.f-sub{height:14px;background:var(--subscribe);color:var(--footer);font-size:6.5px;text-align:center;line-height:14px;width:112px;margin-top:3px;letter-spacing:.3px}
.f-rule{position:absolute;left:53px;width:389px;border-top:1px solid #4b3a34}
.social{position:absolute;display:flex;gap:5px}
.social span{width:15px;height:15px;border:1px solid var(--footer-text);border-radius:50%}
.copyright{position:absolute;right:53px;font-size:5.8px;color:#eee}
</style>
</head>
<body>
<div class="board">

<div class="sample-label" style="left:309px">Sample 1</div>
<div class="sample-label" style="left:873px">Sample 2</div>
<div class="sample-label" style="left:1438px">Sample 3</div>

<!-- ============ Option 1 ============ -->
<section class="page" style="left:211px;height:1434px">
  <span class="nav-link active" style="left:52px">HOME</span>
  <span class="nav-link" style="left:87px">ABOUT ME</span>
  <span class="nav-link" style="left:137px">SERVICES</span>
  <div class="brand" style="top:22px">VIRELA</div>
  <span class="nav-link low" style="left:313px">INSTALLATION</span>
  <span class="nav-link low" style="left:372px">CLIENTS</span>
  <span class="nav-link low" style="left:411px">CONTACT</span>
  <div class="arc"></div>

  <h1 class="headline">MASTER THE ART OF HAIR EXTENSIONS!</h1>
  <p class="subhead">JOIN OUR COMPREHENSIVE 1 ON 1 COURSE TODAY!</p>
  <div class="rule"></div>
  <p class="intro">Are you passionate about weave hair extensions and want to expand your skillset? Look no further! We are thrilled to offer you an exclusive opportunity to learn the art of Weave hair extensions through our comprehensive course.</p>
  <h2 class="section-title">COURSE HIGHLIGHTS:</h2>

  <div class="icon-box" style="left:79px;top:229px"><div class="art" role="img" aria-label="Line icon of a head with hair wefts"></div></div>
  <div class="item" style="left:167px;top:237px"><h3>1. THREE TECHNIQUES OF WEFTING:</h3><p>Unlock the secrets of three different wefting techniques. Our expert instructor will guide you through each technique, providing in-depth knowledge and hands-on practice to master the art of hair extension application.</p></div>

  <div class="item" style="left:79px;top:334px;width:250px"><h3>2. PREMIUM HAIR BUNDLES:</h3><p>We believe in providing the best materials for our students. Receive four bundles of high-quality, 25-gram hair extensions that are perfect for practicing the techniques taught in the course. Explore various hair types, textures, and colors to cater to diverse client preferences.</p></div>
  <div class="icon-box" style="left:334px;top:325px"><div class="art" role="img" aria-label="Line icon of hair bundles"></div></div>

  <div class="icon-box" style="left:79px;top:421px"><div class="art" role="img" aria-label="Line icon of hair extension tools"></div></div>
  <div class="item" style="left:167px;top:427px"><h3>3.FREE HAIR EXTENSION TOOLS:</h3><p>We've got you covered! As part of the course, we provide a complimentary set of essential hair extension tools, including weaving needles, thread, clips, sectioning combs, hair extension pliers, and more. With these professional tools in your arsenal, you'll be ready to create stunning transformations.</p></div>

  <div class="item" style="left:79px;top:523px;width:245px"><h3>4. COMPREHENSIVE EDUCATION:</h3><p>Our course offers a well-rounded education that covers everything you need to know about hair extensions. From client consultation to hair preparation, proper application techniques, maintenance, and removal, our curriculum ensures you gain the knowledge and confidence to excel as a hair extension specialist.</p></div>
  <div class="icon-box" style="left:334px;top:514px"><div class="art" role="img" aria-label="Line icon of a graduation cap"></div></div>

  <div class="icon-box" style="left:79px;top:611px"><div class="art" role="img" aria-label="Line icon of a rolled certificate"></div></div>
  <div class="item" style="left:167px;top:619px"><h3>4.CERTIFICATE OF COMPLETION:</h3><p>Upon successfully finishing the course, you'll receive a prestigious certificate of completion. This recognition will elevate your professional profile and help you stand out in the competitive beauty industry.</p></div>

  <p class="closing" style="top:710px">Don't miss this incredible opportunity to advance your skills and expand your career possibilities. Enroll in our hair extension course today and unleash your creativity!</p>

  <div class="details details-s1"><h2>COURSE DETAILS</h2><p><b>Duration:</b> [ 2 Full day Course ]<br><b>Location:</b> [14 Wattle Lane Bayview]<br><b>Investment:</b> $3999 payment options available</p></div>

  <div class="form-box" style="top:938px;height:249px"></div>
  <h2 class="form-title" style="top:958px">REGISTRATION FORM</h2>
  <p class="form-sub" style="top:984px">“”fill out the form below “”</p>
  <div class="line-field" style="left:118px;top:1018px">First Name:</div>
  <div class="line-field" style="left:253px;top:1018px">Last Name:</div>
  <div class="line-field" style="left:118px;top:1048px">Email:</div>
  <div class="line-field" style="left:253px;top:1048px">Phone:</div>
  <div class="line-field" style="left:118px;top:1078px">DOB<span class="glyph">▦</span></div>
  <div class="line-field" style="left:253px;top:1078px">Gender<span class="glyph">⌄</span></div>
  <div class="line-field" style="left:118px;top:1108px">Address</div>
  <div class="line-field" style="left:253px;top:1108px">State/Pincode</div>
  <div class="line-field" style="left:118px;top:1134px;width:258px;height:30px">Message</div>
  <div class="submit" style="left:214px;top:1176px">SUBMIT</div>

  <footer class="footer" style="top:1236px;height:198px">
    <div class="brand" style="top:26px">VIRELA</div>
    <div class="f-col" style="left:53px;top:73px"><h4>OPENING TIMES</h4>Monday to Friday 10am – 8pm<br>Saturday 11am – 5pm<br>Closed on Bank Holidays.</div>
    <div class="f-col" style="left:186px;top:73px"><h4>CONTACT US</h4><span class="pin">●</span>Location:<br><span class="pin"></span>Melbourne, Victoria Australia<br><span class="pin">✆</span>Call Us: 555 010 2468<br><span class="pin">✉</span>info@virelahairextensions.com</div>
    <div class="f-col" style="left:331px;top:73px"><h4>LET'S KEEP IN TOUCH</h4><div class="f-email">Email:</div><div class="f-sub">SUBSCRIBE</div></div>
    <div class="f-rule" style="top:155px"></div>
    <div class="social" style="left:53px;top:170px" role="img" aria-label="Social media links"><span></span><span></span><span></span></div>
    <div class="copyright" style="top:176px">2023 © Copyright Virela Hair Extensions. All Rights Reserved.</div>
  </footer>
</section>

<!-- ============ Option 2 ============ -->
<section class="page" style="left:775px;height:1403px">
  <span class="nav-link active" style="left:52px">HOME</span>
  <span class="nav-link" style="left:87px">ABOUT ME</span>
  <span class="nav-link" style="left:137px">SERVICES</span>
  <div class="brand" style="top:22px">VIRELA</div>
  <span class="nav-link low" style="left:313px">INSTALLATION</span>
  <span class="nav-link low" style="left:372px">CLIENTS</span>
  <span class="nav-link low" style="left:411px">CONTACT</span>
  <div class="arc"></div>

  <h1 class="headline">MASTER THE ART OF HAIR EXTENSIONS!</h1>
  <p class="subhead">JOIN OUR COMPREHENSIVE 1 ON 1 COURSE TODAY!</p>
  <div class="rule"></div>
  <p class="intro">Are you passionate about weave hair extensions and want to expand your skillset? Look no further! We are thrilled to offer you an exclusive opportunity to learn the art of Weave hair extensions through our comprehensive course.</p>
  <h2 class="section-title">COURSE HIGHLIGHTS:</h2>

  <div class="icon-box" style="left:79px;top:229px"><div class="art" role="img" aria-label="Line icon of a head with hair wefts"></div></div>
  <div class="item" style="left:167px;top:237px"><h3>1. THREE TECHNIQUES OF WEFTING:</h3><p>Unlock the secrets of three different wefting techniques. Our expert instructor will guide you through each technique, providing in-depth knowledge and hands-on practice to master the art of hair extension application.</p></div>
  <div class="icon-box" style="left:79px;top:316px"><div class="art" role="img" aria-label="Line icon of hair bundles"></div></div>
  <div class="item" style="left:167px;top:325px"><h3>2. PREMIUM HAIR BUNDLES:</h3><p>We believe in providing the best materials for our students. Receive four bundles of high-quality, 25-gram hair extensions that are perfect for practicing the techniques taught in the course. Explore various hair types, textures, and colors to cater to diverse client preferences.</p></div>
  <div class="icon-box" style="left:79px;top:403px"><div class="art" role="img" aria-label="Line icon of hair extension tools"></div></div>
  <div class="item" style="left:167px;top:408px"><h3>3.FREE HAIR EXTENSION TOOLS:</h3><p>We've got you covered! As part of the course, we provide a complimentary set of essential hair extension tools, including weaving needles, thread, clips, sectioning combs, hair extension pliers, and more. With these professional tools in your arsenal, you'll be ready to create stunning transformations.</p></div>
  <div class="icon-box" style="left:79px;top:487px"><div class="art" role="img" aria-label="Line icon of a graduation cap"></div></div>
  <div class="item" style="left:167px;top:490px"><h3>4. COMPREHENSIVE EDUCATION:</h3><p>Our course offers a well-rounded education that covers everything you need to know about hair extensions. From client consultation to hair preparation, proper application techniques, maintenance, and removal, our curriculum ensures you gain the knowledge and confidence to excel as a hair extension specialist.</p></div>
  <div class="icon-box" style="left:79px;top:568px"><div class="art" role="img" aria-label="Line icon of a rolled certificate"></div></div>
  <div class="item" style="left:167px;top:577px"><h3>4.CERTIFICATE OF COMPLETION:</h3><p>Upon successfully finishing the course, you'll receive a prestigious certificate of completion. This recognition will elevate your professional profile and help you stand out in the competitive beauty industry.</p></div>

  <p class="closing" style="top:661px">Don't miss this incredible opportunity to advance your skills and expand your career possibilities. Enroll in our hair extension course today and unleash your creativity!</p>

  <div class="details details-s2"><h2>COURSE DETAILS</h2><p><b>Duration:</b> [ 2 Full day Course ]<br><b>Location:</b> [14 Wattle Lane Bayview]<br><b>Investment:</b> $3999 payment options available</p></div>

  <div class="form-box" style="top:910px;height:248px"></div>
  <h2 class="form-title" style="top:929px">REGISTRATION FORM</h2>
  <p class="form-sub" style="top:955px">“”fill out the form below “”</p>
  <div class="line-field" style="left:118px;top:990px">First Name:</div>
  <div class="line-field" style="left:253px;top:990px">Last Name:</div>
  <div class="line-field" style="left:118px;top:1020px">Email:</div>
  <div class="line-field" style="left:253px;top:1020px">Phone:</div>
  <div class="line-field" style="left:118px;top:1050px">DOB<span class="glyph">▦</span></div>
  <div class="line-field" style="left:253px;top:1050px">Gender<span class="glyph">⌄</span></div>
  <div class="line-field" style="left:118px;top:1080px">Address</div>
  <div class="line-field" style="left:253px;top:1080px">State/Pincode</div>
  <div class="line-field" style="left:118px;top:1106px;width:258px;height:30px">Message</div>
  <div class="submit" style="left:213px;top:1147px">SUBMIT</div>

  <footer class="footer" style="top:1207px;height:196px">
    <div class="brand" style="top:26px">VIRELA</div>
    <div class="f-col" style="left:53px;top:73px"><h4>OPENING TIMES</h4>Monday to Friday 10am – 8pm<br>Saturday 11am – 5pm<br>Closed on Bank Holidays.</div>
    <div class="f-col" style="left:186px;top:73px"><h4>CONTACT US</h4><span class="pin">●</span>Location:<br><span class="pin"></span>Melbourne, Victoria Australia<br><span class="pin">✆</span>Call Us: 555 010 2468<br><span class="pin">✉</span>info@virelahairextensions.com</div>
    <div class="f-col" style="left:331px;top:73px"><h4>LET'S KEEP IN TOUCH</h4><div class="f-email">Email:</div><div class="f-sub">SUBSCRIBE</div></div>
    <div class="f-rule" style="top:155px"></div>
    <div class="social" style="left:53px;top:168px" role="img" aria-label="Social media links"><span></span><span></span><span></span></div>
    <div class="copyright" style="top:174px">2023 © Copyright Virela Hair Extensions. All Rights Reserved.</div>
  </footer>
</section>

<!-- ============ Option 3 ============ -->
<section class="page" style="left:1338px;height:1349px">
  <span class="nav-link active" style="left:52px">HOME</span>
  <span class="nav-link" style="left:87px">ABOUT ME</span>
  <span class="nav-link" style="left:137px">SERVICES</span>
  <div class="brand" style="top:22px">VIRELA</div>
  <span class="nav-link low" style="left:313px">INSTALLATION</span>
  <span class="nav-link low" style="left:372px">CLIENTS</span>
  <span class="nav-link low" style="left:411px">CONTACT</span>
  <div class="arc"></div>

  <h1 class="headline">MASTER THE ART OF HAIR EXTENSIONS!</h1>
  <p class="subhead">JOIN OUR COMPREHENSIVE 1 ON 1 COURSE TODAY!</p>
  <div class="rule"></div>
  <p class="intro">Are you passionate about weave hair extensions and want to expand your skillset? Look no further! We are thrilled to offer you an exclusive opportunity to learn the art of Weave hair extensions through our comprehensive course.</p>
  <h2 class="section-title">COURSE HIGHLIGHTS:</h2>

  <div class="icon-circle" style="left:88px;top:227px"><div class="art" role="img" aria-label="Line icon of a head with hair wefts"></div></div>
  <span class="num" style="left:78px;top:246px">1</span>
  <div class="item" style="left:167px;top:237px"><h3>THREE TECHNIQUES OF WEFTING:</h3><p>Unlock the secrets of three different wefting techniques. Our expert instructor will guide you through each technique, providing in-depth knowledge and hands-on practice to master the art of hair extension application.</p></div>
  <div class="icon-circle" style="left:88px;top:314px"><div class="art" role="img" aria-label="Line icon of hair bundles"></div></div>
  <span class="num" style="left:78px;top:333px">2</span>
  <div class="item" style="left:167px;top:325px"><h3>2. PREMIUM HAIR BUNDLES:</h3><p>We believe in providing the best materials for our students. Receive four bundles of high-quality, 25-gram hair extensions that are perfect for practicing the techniques taught in the course. Explore various hair types, textures, and colors to cater to diverse client preferences.</p></div>
  <div class="icon-circle" style="left:88px;top:401px"><div class="art" role="img" aria-label="Line icon of hair extension tools"></div></div>
  <span class="num" style="left:78px;top:420px">3</span>
  <div class="item" style="left:167px;top:408px"><h3>3.FREE HAIR EXTENSION TOOLS:</h3><p>We've got you covered! As part of the course, we provide a complimentary set of essential hair extension tools, including weaving needles, thread, clips, sectioning combs, hair extension pliers, and more. With these professional tools in your arsenal, you'll be ready to create stunning transformations.</p></div>
  <div class="icon-circle" style="left:88px;top:485px"><div class="art" role="img" aria-label="Line icon of a graduation cap"></div></div>
  <span class="num" style="left:78px;top:504px">4</span>
  <div class="item" style="left:167px;top:490px"><h3>4. COMPREHENSIVE EDUCATION:</h3><p>Our course offers a well-rounded education that covers everything you need to know about hair extensions. From client consultation to hair preparation, proper application techniques, maintenance, and removal, our curriculum ensures you gain the knowledge and confidence to excel as a hair extension specialist.</p></div>
  <div class="icon-circle" style="left:88px;top:566px"><div class="art" role="img" aria-label="Line icon of a rolled certificate"></div></div>
  <span class="num" style="left:78px;top:585px">5</span>
  <div class="item" style="left:167px;top:577px"><h3>4.CERTIFICATE OF COMPLETION:</h3><p>Upon successfully finishing the course, you'll receive a prestigious certificate of completion. This recognition will elevate your professional profile and help you stand out in the competitive beauty industry.</p></div>

  <p class="closing" style="top:661px">Don't miss this incredible opportunity to advance your skills and expand your career possibilities. Enroll in our hair extension course today and unleash your creativity!</p>

  <div class="details details-s3"><h2>COURSE DETAILS</h2><p><b>Duration:</b> [ 2 Full day Course ]<br><b>Location:</b> [14 Wattle Lane Bayview]<br><b>Investment:</b> $3999 payment options available</p></div>

  <div class="band" style="top:872px;height:284px"></div>
  <h2 class="form-title" style="top:903px">REGISTRATION FORM</h2>
  <p class="form-sub" style="top:929px">“”fill out the form below “”</p>
  <div class="box-field" style="left:116px;top:958px">First Name:</div>
  <div class="box-field" style="left:249px;top:958px">Last Name:</div>
  <div class="box-field" style="left:116px;top:982px">Email:</div>
  <div class="box-field" style="left:249px;top:982px">Phone:</div>
  <div class="box-field" style="left:116px;top:1008px">DOB<span class="glyph" style="top:6px">▦</span></div>
  <div class="box-field" style="left:249px;top:1008px">Gender<span class="glyph" style="top:5px">⌄</span></div>
  <div class="box-field" style="left:116px;top:1033px">Address</div>
  <div class="box-field" style="left:249px;top:1033px">State/Pincode</div>
  <div class="box-field" style="left:116px;top:1059px;width:260px;height:49px">Message</div>
  <div class="submit" style="left:212px;top:1099px;height:20px;line-height:18px">SUBMIT</div>

  <footer class="footer" style="top:1156px;height:193px">
    <div class="brand" style="top:23px">VIRELA</div>
    <div class="f-col" style="left:53px;top:71px"><h4>OPENING TIMES</h4>Monday to Friday 10am – 8pm<br>Saturday 11am – 5pm<br>Closed on Bank Holidays.</div>
    <div class="f-col" style="left:186px;top:71px"><h4>CONTACT US</h4><span class="pin">●</span>Location:<br><span class="pin"></span>Melbourne, Victoria Australia<br><span class="pin">✆</span>Call Us: 555 010 2468<br><span class="pin">✉</span>info@virelahairextensions.com</div>
    <div class="f-col" style="left:331px;top:71px"><h4>LET'S KEEP IN TOUCH</h4><div class="f-email">Email:</div><div class="f-sub">SUBSCRIBE</div></div>
    <div class="f-rule" style="top:156px"></div>
    <div class="social" style="left:53px;top:169px" role="img" aria-label="Social media links"><span></span><span></span><span></span></div>
    <div class="copyright" style="top:175px">2023 © Copyright Virela Hair Extensions. All Rights Reserved.</div>
  </footer>
</section>

</div>
</body>
</html>
```